Website for Vornelix Capital, my new firm that raises money from investors to buy, build, own an...

Vornelix Capital needs a website! We are a new company with very experienced people, who invest in, own and build hotel properties, as well as apartments and other commercial real estate. We seek investors for our projects, and we provide safe, secure returns on their investment in our projects. Our new logo is designed to exhibit strength, class and security, and would like our website to continue on this theme. Our name, Vornelix, is a word-play on a Greek word “aristeia”, which means “excellence” and “a warriors finest moment of glory in war”. If you are in business, you realize that much of it is like war, with strategy and moves and opponents and competitors, and ever-changing economic conditions and threats that make business very much like war. We like to think that we are good at business (war), and so have named our company “Vornelix”, using the founders last name and the word “aristeia” combined. Another definition of "aristeia" is "performing at the peak of one's potential after a long struggle"...again, much like business in real life! The website design should exhibit financial security, smart moves, and positive growth towards a bright future.

Target Market(s)

The target market is smart and wealthy investors, with others such as brokers, cities and government agencies, lenders, sellers, partners, etc also looking at it.

Industry/Entity Type

Investment

Number of Pages Required

5+ page

Font styles to use
Sans Serif

Colors
fec214

Requirements
Must have
• Our website should have a landing page, a "about" or bio page, a projects page and a contact us page. Our new logo uses the colors black and gold, so this should be factored in to our site. The site should be simple, yet impactful and impressive. I have actually two logos, which can be mixed and interchanged in a complimentary way, each with their own unique look.
Nice to have
• I have uploaded a couple screenshots of a website i like, and the simplicity I mention.
Should not have
• The site should not be flashy or complicated or complex or "busy"

```html
<!DOCTYPE html>
<html lang="en">
<head>
<meta charset="utf-8">
<title>Vornelix Capital</title>
<link rel="stylesheet" href="https://fonts.googleapis.com/css2?family=Merriweather+Sans:wght@400;700;800&family=Open+Sans:ital,wght@0,400;0,600;1,400&display=swap">
<style>
  :root{
    --gold:#c4952e;
    --ink:#2b2b2b;
    --body:#555555;
    --white:#ffffff;
    --line:#d9d9d9;
    --dark:#333333;
  }
  *{margin:0;padding:0;box-sizing:border-box}
  html,body{width:1200px;height:2875px;overflow:hidden}
  body{position:relative;font-family:"Open Sans",sans-serif;color:var(--body);background:var(--white)}
  .abs{position:absolute}
  .heading{font-family:"Merriweather Sans",sans-serif;font-weight:700;color:var(--ink)}

  .topbar{left:0;top:0;width:1200px;height:42px;background:var(--gold);color:var(--white);font-size:14px}
  .topbar span{position:absolute;top:11px}

  .nav{left:0;top:42px;width:1200px;height:92px;background:var(--white)}
  .brand{left:77px;top:30px;font-family:"Merriweather Sans",sans-serif;font-weight:700;font-size:20px;color:var(--ink);letter-spacing:1px}
  .nav a{position:absolute;top:35px;font-size:14px;color:#444;text-decoration:none}
  .nav a.active{color:var(--gold)}

  .hero{left:0;top:134px;width:1200px;height:585px;background:linear-gradient(100deg,#b9c3c4 0%,#d7dcdc 35%,#eceeee 60%,#f6f6f6 100%)}
  .hero-title{left:659px;top:326px;font-size:41px;line-height:58px;letter-spacing:.5px}

  .services{left:0;top:719px;width:1200px;height:583px;background:var(--gold)}
  .services-art{left:77px;top:828px;width:561px;height:400px;background:linear-gradient(150deg,#f4f4f4,#d7dde2 60%,#eef0f2);border-radius:14px}
  .service-icon{left:687px;width:52px;height:52px}
  .service-title{left:773px;font-family:"Merriweather Sans",sans-serif;font-weight:700;font-size:23px;color:var(--white)}
  .service-text{left:692px;width:400px;font-size:14px;line-height:25px;color:var(--white)}

  .about-title{left:0;width:1200px;top:1354px;text-align:center;font-size:38px}
  .about-text{left:230px;width:740px;text-align:center;font-size:14.5px;line-height:25px}

  .projects{left:0;top:1645px;width:1200px;height:479px;background:linear-gradient(115deg,#f3f7fa 0%,#dfe9f0 45%,#eef3f7 70%,#d5e1ea 100%)}
  .projects-title{left:0;width:1200px;top:1697px;text-align:center;font-size:38px}
  .project-name{left:79px;top:1804px;font-size:28px}
  .project-text{left:79px;width:470px;font-size:14.5px;line-height:25px;color:#333}
  .project-art{left:667px;top:1779px;width:458px;height:263px;background:linear-gradient(160deg,#9cb6cf,#4f6e8e 55%,#2c3e52);border-radius:10px}
  .arrow{top:1908px;width:30px;height:30px}

  .contact-title{left:0;width:1200px;top:2176px;text-align:center;font-size:38px}
  .field{height:40px;border-bottom:2px solid var(--line);font-size:14px;color:#555;padding:11px 12px 0}
  .send{left:516px;top:2390px;width:166px;height:47px;background:var(--gold);color:var(--white);font-family:"Merriweather Sans",sans-serif;font-weight:700;font-size:19px;text-align:center;line-height:47px;border-radius:3px}

  .footer{left:0;top:2521px;width:1200px;height:291px;background:var(--gold);color:var(--white)}
  .footer-brand{left:77px;top:2597px;font-family:"Merriweather Sans",sans-serif;font-weight:400;font-size:25px;color:var(--white);letter-spacing:1.5px}
  .newsletter{left:77px;top:2661px;width:270px;height:46px;border:1.5px solid var(--white);font-style:italic;font-size:14px;padding:13px 16px;color:var(--white)}
  .footer-heading{top:2573px;font-family:"Merriweather Sans",sans-serif;font-weight:700;font-size:22px;color:var(--white)}
  .sitemap li{position:absolute;list-style:none;font-size:14px;padding-left:28px;color:var(--white)}
  .sitemap li::before{content:"";position:absolute;left:0;top:4px;width:13px;height:13px;border-radius:50%;background:var(--white)}
  .footer-contact{left:836px;font-size:14px;line-height:25px;width:270px;color:var(--white)}
  .copyright{left:0;top:2812px;width:1200px;height:63px;background:var(--dark);color:var(--white);text-align:center;font-size:14px;line-height:63px}
</style>
</head>
<body>

<div class="abs topbar">
  <span style="left:596px">EMAIL US ON : info@vornelix-capital.com</span>
  <span style="left:935px">CALL US ON : 123 456 7890</span>
</div>

<header class="abs nav">
  <div class="abs brand">VORNELIX</div>
  <a class="active" style="left:788px">HOME</a>
  <a style="left:859px">ABOUT</a>
  <a style="left:947px">PROJECTS</a>
  <a style="left:1052px">CONTACT</a>
</header>

<section class="abs hero" role="img" aria-label="Photo of a businesswoman on the phone working at a laptop in a bright modern office"></section>
<h1 class="abs heading hero-title">VORNELIX CAPITAL<br>FOR SAFE AND SECURE<br>RETURNS</h1>

<section class="abs services"></section>
<div class="abs services-art" role="img" aria-label="Two open white laptops showing a business team and financial charts"></div>

<svg class="abs service-icon" style="top:800px" viewBox="0 0 52 52"><circle cx="26" cy="26" r="24" fill="none" stroke="#fff" stroke-width="1.5"/><rect x="19" y="14" width="14" height="24" fill="none" stroke="#fff" stroke-width="1.5"/><path d="M22 19h8M22 24h8M22 29h8" stroke="#fff" stroke-width="1.5"/></svg>
<div class="abs service-title" style="top:812px">Hotel properties</div>
<p class="abs service-text" style="top:868px">Lorem Ipsum is simply dummy text of the printing and typesetting industry. Lorem Ipsum has been the industry.</p>

<svg class="abs service-icon" style="top:949px" viewBox="0 0 52 52"><circle cx="26" cy="26" r="24" fill="none" stroke="#fff" stroke-width="1.5"/><rect x="18" y="17" width="16" height="21" fill="none" stroke="#fff" stroke-width="1.5"/><path d="M21 22h4M27 22h4M21 27h4M27 27h4M21 32h4M27 32h4" stroke="#fff" stroke-width="1.5"/></svg>
<div class="abs service-title" style="top:958px">Apartments</div>
<p class="abs service-text" style="top:1014px">Lorem Ipsum is simply dummy text of the printing and typesetting industry. Lorem Ipsum has been the industry.</p>

<svg class="abs service-icon" style="top:1095px" viewBox="0 0 52 52"><circle cx="26" cy="26" r="24" fill="none" stroke="#fff" stroke-width="1.5"/><rect x="16" y="20" width="10" height="18" fill="none" stroke="#fff" stroke-width="1.5"/><rect x="26" y="14" width="11" height="24" fill="none" stroke="#fff" stroke-width="1.5"/><path d="M29 19h5M29 24h5M29 29h5M19 25h4M19 30h4" stroke="#fff" stroke-width="1.5"/></svg>
<div class="abs service-title" style="top:1105px">Commercial real estate</div>
<p class="abs service-text" style="top:1161px">Lorem Ipsum is simply dummy text of the printing and typesetting industry. Lorem Ipsum has been the industry.</p>

<h2 class="abs heading about-title">ABOUT US</h2>
<p class="abs about-text" style="top:1408px">Lorem Ipsum is simply dummy text of the printing and typesetting industry. Lorem Ipsum has been the industry's standard dummy text ever since the 1500s, when an unknown printer took a galley of type and scrambled it to make a type specimen book. It has survived not only five centuries, but also the leap into electronic typesetting, remaining essentially unchanged.</p>
<p class="abs about-text" style="top:1522px">It was popularised in the 1960s with the release of Typorin sheets containing Lorem Ipsum passages, and more recently with desktop publishing software like Quillby PageMaster including versions of Lorem Ipsum.</p>

<section class="abs projects" role="img" aria-label="Soft background photo of glass office tower facades"></section>
<h2 class="abs heading projects-title">RECENT PROJECTS</h2>
<h3 class="abs heading project-name">PROJECT NAME</h3>
<p class="abs project-text" style="top:1843px">Lorem Ipsum is simply dummy text of the printing and typesetting industry. Lorem Ipsum has been the industry's standard dummy text ever since the 1500s, when an unknown printer took a galley of type and scrambled it to make a type specimen book.</p>
<p class="abs project-text" style="top:1955px">It was popularised in the 1960s with the release of Typorin sheets containing Lorem Ipsum passages, and more recently.</p>
<div class="abs project-art" role="img" aria-label="Laptop showing a modern glass office building"></div>
<svg class="abs arrow" style="left:24px" viewBox="0 0 30 30"><path d="M19 6 10 15l9 9" fill="none" stroke="#222" stroke-width="2.5"/></svg>
<svg class="abs arrow" style="left:1146px" viewBox="0 0 30 30"><path d="M11 6l9 9-9 9" fill="none" stroke="#222" stroke-width="2.5"/></svg>

<h2 class="abs heading contact-title">CONTACT US</h2>
<div class="abs field" style="left:130px;top:2236px;width:292px">Name</div>
<div class="abs field" style="left:452px;top:2236px;width:292px">Email</div>
<div class="abs field" style="left:774px;top:2236px;width:292px">Phone</div>
<div class="abs field" style="left:130px;top:2329px;width:936px">Message</div>
<div class="abs send">SEND</div>

<footer class="abs footer"></footer>
<div class="abs footer-brand">VORNELIX | CAPITAL</div>
<div class="abs newsletter">Email Address</div>
<svg class="abs" style="left:304px;top:2673px" width="24" height="22" viewBox="0 0 24 22"><path d="M1 10 23 1 17 21l-5-7-4 4v-6z" fill="#fff"/></svg>

<div class="abs footer-heading" style="left:441px">SITEMAP</div>
<ul class="sitemap">
  <li class="abs" style="left:441px;top:2618px">Home</li>
  <li class="abs" style="left:441px;top:2657px">About</li>
  <li class="abs" style="left:441px;top:2695px">Projects</li>
  <li class="abs" style="left:441px;top:2733px">Contact</li>
  <li class="abs" style="left:613px;top:2618px">Sitemap</li>
  <li class="abs" style="left:613px;top:2657px">Privacy Policy</li>
</ul>

<div class="abs footer-heading" style="left:801px">CONTACT US</div>
<svg class="abs" style="left:802px;top:2620px" width="16" height="22" viewBox="0 0 16 22"><path d="M8 0a8 8 0 0 0-8 8c0 6 8 14 8 14s8-8 8-14a8 8 0 0 0-8-8zm0 11a3 3 0 1 1 0-6 3 3 0 0 1 0 6z" fill="#fff"/></svg>
<p class="abs footer-contact" style="top:2615px">Lorem Ipsum is simply dummy text of the printing and typesetting industry.</p>
<svg class="abs" style="left:801px;top:2686px" width="18" height="18" viewBox="0 0 18 18"><path d="M4 1l3 4-2 2c1 2 4 5 6 6l2-2 4 3-2 3C8 17 1 10 1 3z" fill="#fff"/></svg>
<p class="abs footer-contact" style="top:2682px">123 456 7890</p>
<svg class="abs" style="left:800px;top:2729px" width="20" height="15" viewBox="0 0 20 15"><rect width="20" height="15" fill="#fff"/><path d="M0 1l10 7 10-7" fill="none" stroke="#c4952e" stroke-width="1.5"/></svg>
<p class="abs footer-contact" style="top:2724px">hello@vornelix-capital.com</p>

<div class="abs copyright">©VORNELIX CAPITAL. 2018 - All Rights Reserved.</div>

</body>
</html>
```